Lune Tavi Wigs " Styling Foam"

I need a label created for my product . The bottle size is 50ml so it must be designed to fit that size bottle. I will post my logo and examples of my bottle size. I want the label design to be simple and cute. ill also add pictures of my website, so you can get ideas from there. The bottle is white so I want the main colors to be white and pink. All colors on the label must match my logo. I love glitter as well.

I know for sure I want my logo big, and I want "Styling Foam'',
then under styling foam I would like " Medium Hold" in a different front. be very creative.

Then under that I would like it to say " No Alcohol , Saulfate or Paraben

please make sure on the label in the front it has "NET: 7.0 oz / 200g" so people know what size it is.

I would like a glitter border on the label.

I also want the back of the label to have directions.

And ingredients list too . Very small not too big at all.

Target Market(s)

My target market is woman of all ages .. but mainly woman from ages 26-65

Industry/Entity Type

Hair And Beauty

Font styles to use
Serif
Sans Serif
Decorative
Script

Colors
e667a6
eda3c7
f9d9e8
e34297

Requirements
Must have
• The project must match the colors of my logo, it must have a nice pretty glitter border . It must be simple and clean . But still stylish ! I don’t want everything after my logo to be in the same font . Have fun with this design, be creative. My logo and “ Styling Foam” must be the two centerpiece!
Nice to have
• It will be nice to have different fonts! And nice to have all the colors that match my logo
Must be expensive looking !!
Very eye catching!
Should not have
• Do not add colors that my logo doesn’t have !!!!
I don’t want it to look too plain and boring ! I want it to be classy and expensive looking !

```html
<!DOCTYPE html>
<html lang="en">
<head>
<meta charset="utf-8">
<title>Lune Tavi Wigs – Styling Foam Labels</title>
<link rel="stylesheet" href="https://fonts.googleapis.com/css2?family=Zilla+Slab:wght@500;600&family=Kaushan+Script&family=Permanent+Marker&family=Yellowtail&family=Open+Sans:wght@700&display=swap">
<style>
  :root {
    --backdrop: #6b7fa6;
    --label-white: #ffffff;
    --label-black: #0b0b0d;
    --pink-deep: #e34297;
    --pink: #e667a6;
    --pink-soft: #eda3c7;
    --pink-blush: #f9d9e8;
    --magenta: #b81fbf;
    --magenta-dark: #3a0b3d;
    --hold-bronze: #c8662b;
    --text-white: #ffffff;
    --net-black: #111111;
  }
  * { margin: 0; padding: 0; box-sizing: border-box; }
  html, body { width: 1200px; height: 975px; overflow: hidden; }
  body { background: var(--backdrop); position: relative; }

  .label { position: absolute; top: 365px; height: 525px; overflow: hidden; }
  .label--light { left: 283px; width: 232px; background: var(--label-white); }
  .label--dark  { left: 652px; width: 248px; background: var(--label-black); }

  .label > * { position: absolute; left: 0; right: 0; text-align: center; margin: 0 auto; }

  .brand-name {
    font-family: "Zilla Slab", serif;
    font-weight: 600;
    color: var(--pink-deep);
    line-height: 1.05;
  }
  .label--light .brand-name { top: 52px; font-size: 30px; }
  .label--dark .brand-name { top: 92px; font-size: 22px; z-index: 1; }

  .swirl-art {
    top: 160px; width: 160px; height: 170px;
    background: linear-gradient(160deg, var(--pink-blush), var(--pink-soft) 55%, var(--pink) 100%);
    border-radius: 4px;
    opacity: 0.8;
  }

  .product-title--serif {
    top: 337px;
    font-family: "Zilla Slab", serif;
    font-weight: 500;
    color: var(--pink-deep);
    font-size: 28px;
    line-height: 1;
  }
  .hold--script {
    top: 406px;
    font-family: "Kaushan Script", cursive;
    color: var(--hold-bronze);
    font-size: 26px;
    line-height: 1.2;
  }

  .badges { display: flex; justify-content: center; gap: 8px; }
  .badge { width: 18px; height: 18px; border-radius: 50%; background: var(--pink-deep); }
  .label--light .badges { top: 450px; }
  .label--dark .badges { top: 480px; }
  .label--dark .badge { width: 15px; height: 15px; background: none; border: 1.5px solid var(--pink-deep); }

  .net-weight {
    font-family: "Open Sans", sans-serif;
    font-weight: 700;
    font-size: 10px;
    line-height: 16px;
    color: var(--text-white);
    width: max-content;
  }
  .label--light .net-weight { top: 478px; background: var(--net-black); border-radius: 8px; padding: 0 10px; }
  .label--dark .net-weight { top: 501px; }

  .pattern-area {
    background: linear-gradient(180deg, var(--magenta-dark), var(--magenta) 50%, var(--magenta-dark));
  }
  .pattern-area--upper { top: 8px; height: 215px; }
  .pattern-area--lower { top: 415px; height: 110px; }

  .product-title--brush {
    top: 248px;
    font-family: "Permanent Marker", cursive;
    color: var(--pink-deep);
    font-size: 40px;
    line-height: 1.05;
  }
  .hold--white {
    top: 360px;
    font-family: "Yellowtail", cursive;
    color: var(--text-white);
    font-size: 34px;
    line-height: 1.2;
  }
</style>
</head>
<body>

  <section class="label label--light" aria-label="White styling foam label">
    <h1 class="brand-name">Lune Tavi<br>Wigs</h1>
    <div class="swirl-art" role="img" aria-label="Soft pink flowing ribbon swirl illustration"></div>
    <h2 class="product-title--serif">STYLING<br>FOAM</h2>
    <p class="hold--script">Medium Hold</p>
    <div class="badges"><span class="badge"></span><span class="badge"></span></div>
    <p class="net-weight">NET: 7.0 oz / 200g</p>
  </section>

  <section class="label label--dark" aria-label="Black styling foam label">
    <div class="pattern-area pattern-area--upper" role="img" aria-label="Decorative magenta dot pattern behind the brand name"></div>
    <h1 class="brand-name">Lune Tavi<br>Wigs</h1>
    <h2 class="product-title--brush">STYLING<br>FOAM</h2>
    <p class="hold--white">Medium Hold</p>
    <div class="pattern-area pattern-area--lower" role="img" aria-label="Decorative magenta dot pattern"></div>
    <div class="badges"><span class="badge"></span><span class="badge"></span></div>
    <p class="net-weight">NET: 7.0 oz / 200g</p>
  </section>

</body>
</html>
```